Business Card Design For Office Furniture Clearance Company

Kestrel Office Clearance - our company name pretty much explains what we do, we clear offices for high end clients, mainly plc's and large international companies.

We require a nice looking business card that displays professionalism but without being too serious.

It would be nice to see just a little more than a conventional boring business card, make sure you add some flare.

Industry/Entity Type

Office Furniture

Contact Information for Business Card

CARD 1

Mark Holloway
Director
mark@kestrelofficeclearance.co.uk
m: 07700 153928

t: 01632 960418
www.kestrelofficeclearance.co.uk

Kestrel Office Clearance
Unit K4 B
2-8 Fenwick Lane
Bletchley
Milton Keynes
ZZ9 4QT

free office clearances… you cant get better than that.

CARD 2

Peter Radford
Director
peter@kestrelofficeclearance.co.uk
m: 07700 382615

t: 01632 960418

Kestrel Office Clearance
Unit K4 B
2-8 Fenwick Lane
Bletchley
Milton Keynes
ZZ9 4QT

Font styles to use
Sans Serif

Requirements
Must have
• A white background - as we have a blue logo.
Nice to have
• Nice use of the logo - play around with this and dissect it.

```html
<!DOCTYPE html>
<html lang="en">
<head>
<meta charset="utf-8">
<title>Kestrel Office Clearance – Business Cards</title>
<link rel="stylesheet" href="https://fonts.googleapis.com/css2?family=Open+Sans:wght@400;600;700&display=swap">
<style>
  :root {
    --blue: #1b80c6;
    --blue-deep: #1367a6;
    --blue-mark: #1877bd;
    --white: #ffffff;
    --ink-grey: #6b6b6b;
    --page: #e9ebee;
  }
  * { box-sizing: border-box; margin: 0; padding: 0; }
  html, body { width: 1200px; height: 950px; overflow: hidden; }
  body {
    background: var(--page);
    font-family: "Open Sans", sans-serif;
    position: relative;
  }
  .card {
    position: absolute;
    top: 155px;
    width: 400px;
    height: 640px;
    overflow: hidden;
    box-shadow: 0 6px 18px rgba(0,0,0,0.18);
  }
  .card--front {
    left: 160px;
    background: linear-gradient(160deg, var(--blue) 0%, var(--blue-deep) 100%);
    color: var(--white);
  }
  .front__arc {
    position: absolute;
    width: 520px;
    height: 520px;
    border-radius: 50%;
    background: var(--white);
    left: 50%;
    top: -255px;
    transform: translateX(-50%);
  }
  .brand {
    position: absolute;
    left: 0; right: 0;
    display: flex;
    flex-direction: column;
    align-items: center;
  }
  .brand__dot {
    border-radius: 50%;
    background: var(--blue-mark);
  }
  .brand__name {
    font-weight: 700;
    color: var(--blue-mark);
  }
  .card--front .brand { top: 40px; gap: 12px; }
  .card--front .brand__dot { width: 120px; height: 120px; }
  .card--front .brand__name { font-size: 17px; }

  .front__details {
    position: absolute;
    top: 290px;
    left: 36px;
    right: 36px;
    text-align: right;
  }
  .person__name {
    font-size: 24px;
    font-weight: 600;
    letter-spacing: 0.5px;
    text-transform: uppercase;
    line-height: 1.1;
  }
  .person__role {
    font-size: 14px;
    text-transform: uppercase;
    letter-spacing: 0.5px;
  }
  .rule {
    border: none;
    border-top: 2px dotted rgba(255,255,255,0.85);
    margin: 12px 0;
  }
  .address { font-size: 15px; line-height: 1.45; font-style: normal; }
  .address__company { font-weight: 700; }
  .contact {
    list-style: none;
    font-size: 15px;
    line-height: 1.55;
  }
  .contact__item { display: flex; align-items: center; gap: 8px; }
  .contact__item--right { justify-content: flex-end; }
  .contact__item svg { width: 14px; height: 14px; flex: none; }

  .card--back {
    left: 640px;
    background: var(--white);
  }
  .card--back .brand { top: 150px; }
  .card--back .brand__dot { width: 210px; height: 210px; }
  .back__footer {
    position: absolute;
    bottom: 70px;
    left: 30px;
    right: 30px;
    text-align: right;
  }
  .back__name {
    font-size: 22px;
    font-weight: 600;
    color: var(--blue-mark);
    margin-bottom: 16px;
  }
  .back__tagline {
    font-size: 14px;
    color: var(--ink-grey);
    line-height: 1.45;
  }
</style>
</head>
<body>
  <section class="card card--front" aria-label="Business card front">
    <div class="front__arc"></div>
    <div class="brand">
      <span class="brand__dot"></span>
      <span class="brand__name">Kestrel Office Clearance</span>
    </div>
    <div class="front__details">
      <p class="person__name">Mark Holloway</p>
      <p class="person__role">Director</p>
      <hr class="rule">
      <address class="address">
        <span class="address__company">Kestrel Office Clearance</span><br>
        Unit K4 B, 2-8 Fenwick Lane<br>
        Harrowby, Westmere, ZZ9 4QT
      </address>
      <hr class="rule">
      <ul class="contact">
        <li class="contact__item contact__item--right">
          <svg viewBox="0 0 16 16"><path fill="#fff" d="M3 1h3l1.5 4-2 1.3a9 9 0 0 0 4.2 4.2L11 8.5l4 1.5v3a2 2 0 0 1-2 2A12 12 0 0 1 1 3a2 2 0 0 1 2-2z"/></svg>
          01632 960418
        </li>
        <li class="contact__item contact__item--right">
          <svg viewBox="0 0 16 16"><rect x="4" y="1" width="8" height="14" rx="1.5" fill="none" stroke="#fff" stroke-width="1.6"/><circle cx="8" cy="12.5" r="0.9" fill="#fff"/></svg>
          07700 153928
        </li>
        <li class="contact__item">
          <svg viewBox="0 0 16 16"><rect x="1" y="3" width="14" height="10" rx="1" fill="#fff"/><path d="M1.5 3.5 8 9l6.5-5.5" fill="none" stroke="#1b80c6" stroke-width="1.3"/></svg>
          mark@kestrelofficeclearance.co.uk
        </li>
        <li class="contact__item">
          <svg viewBox="0 0 16 16"><circle cx="8" cy="8" r="7" fill="#fff"/><path d="M1 8h14M8 1c-3 3.5-3 10.5 0 14M8 1c3 3.5 3 10.5 0 14" fill="none" stroke="#1b80c6" stroke-width="1.1"/></svg>
          www.kestrelofficeclearance.co.uk
        </li>
      </ul>
    </div>
  </section>

  <section class="card card--back" aria-label="Business card back">
    <div class="brand">
      <span class="brand__dot"></span>
    </div>
    <div class="back__footer">
      <p class="back__name">Kestrel Office Clearance</p>
      <p class="back__tagline">Clear desks, clear floors . . .<br>every job handled with care.</p>
    </div>
  </section>
</body>
</html>
```